Business Card Design for company

We want new business cards. We'd like something different-- yet still highly professional. Our tagline is Providing leadership, delivering success. Stock photos are ok, as long as they are relevant and look upscale.

Target Market(s)

Architecture/Business Management Consulting/Engineering Consulting

Contact Information for Business Card

dark gray background with pops of blue might be good, but you tell me. You're the designers. Rounded corners might be nice, but again, you tell me.

Font styles to use
Serif
Sans Serif

Colors
3276b5
5c5c5c
9d9d9d
fbfbfb

Requirements
Nice to have
• Something different, but still very professional.

```html
<!DOCTYPE html>
<html lang="en">
<head>
<meta charset="UTF-8">
<title>Norvale Partners — Business Cards</title>
<link rel="stylesheet" href="https://fonts.googleapis.com/css2?family=Montserrat:wght@600&family=Work+Sans:wght@400;500&display=swap">
<style>
  :root {
    --backdrop: #2a2a2a;
    --card: #1c1c1c;
    --card-edge: #262626;
    --silver: #c9c9c9;
    --silver-soft: #9d9d9d;
    --rule: #5c5c5c;
    --light: #fbfbfb;
  }
  * { margin: 0; padding: 0; box-sizing: border-box; }
  html, body {
    width: 1200px; height: 900px; overflow: hidden;
    background: var(--backdrop);
  }
  .canvas {
    position: relative; width: 1200px; height: 900px;
    display: flex; flex-direction: column; align-items: center; justify-content: center; gap: 40px;
  }
  .card {
    position: relative; width: 640px; height: 366px;
    background: linear-gradient(160deg, var(--card-edge), var(--card));
    border-radius: 22px;
    color: var(--silver);
    overflow: hidden;
  }
  .wordmark {
    font-family: "Montserrat", sans-serif; font-weight: 600;
    color: var(--silver); text-transform: uppercase; line-height: 1;
    white-space: nowrap;
  }
  .wordmark .name { display: block; }
  .wordmark .sub { display: block; letter-spacing: 0.06em; }

  /* Front */
  .card-front .wordmark {
    position: absolute; top: 96px; left: 0; right: 0; text-align: center;
  }
  .card-front .wordmark .name { font-size: 78px; letter-spacing: 0.02em; }
  .card-front .wordmark .sub { font-size: 27px; margin-top: 6px; letter-spacing: 0.12em; }
  .web-line {
    position: absolute; left: 90px; right: 90px; bottom: 56px;
    display: flex; align-items: center; gap: 14px;
    font-family: "Work Sans", sans-serif; font-size: 14px; color: var(--silver-soft);
  }
  .web-line .rule { flex: 1; height: 1px; background: var(--rule); }

  /* Back */
  .card-back .wordmark {
    position: absolute; left: 40px; top: 128px; width: 268px; text-align: right;
  }
  .card-back .wordmark .name { font-size: 50px; }
  .card-back .wordmark .sub { font-size: 19px; margin-top: 6px; letter-spacing: 0.1em; }
  .divider {
    position: absolute; left: 336px; top: 96px; width: 2px; height: 180px;
    background: var(--silver-soft);
  }
  .details {
    position: absolute; left: 370px; top: 108px;
    font-family: "Work Sans", sans-serif; color: var(--silver);
  }
  .person { font-size: 23px; font-weight: 500; letter-spacing: 0.08em; text-transform: uppercase; }
  .role { font-size: 14px; color: var(--silver-soft); margin-top: 2px; }
  .address { font-size: 14px; line-height: 1.45; margin-top: 16px; font-style: normal; }
  .contacts { list-style: none; margin-top: 12px; font-size: 15px; }
  .contacts li { display: flex; align-items: center; gap: 9px; margin-top: 4px; }
  .contacts svg { width: 11px; height: 11px; fill: none; stroke: var(--silver-soft); stroke-width: 1.4; }
</style>
</head>
<body>
<main class="canvas">
  <section class="card card-front" aria-label="Card front">
    <div class="wordmark">
      <span class="name">Norvale</span>
      <span class="sub">Partners</span>
    </div>
    <div class="web-line">
      <span class="rule"></span>
      <span class="web">www.norvalepartners.com</span>
      <span class="rule"></span>
    </div>
  </section>

  <section class="card card-back" aria-label="Card back">
    <div class="wordmark">
      <span class="name">Norvale</span>
      <span class="sub">Partners</span>
    </div>
    <div class="divider"></div>
    <div class="details">
      <p class="person">Daniel Harper</p>
      <p class="role">Director</p>
      <address class="address">212 Harbour Lane,<br>Westbury, NZ, 8024</address>
      <ul class="contacts">
        <li>
          <svg viewBox="0 0 12 12" aria-hidden="true"><path d="M3 1.5 L4.5 4 L3.5 5 Q5 7.5 7 8.5 L8 7.5 L10.5 9 L9.5 10.5 Q5 10.5 1.5 3 Z"/></svg>
          (555) 014-2290
        </li>
        <li>
          <svg viewBox="0 0 12 12" aria-hidden="true"><rect x="1" y="2.5" width="10" height="7"/><path d="M1 2.5 L6 6.5 L11 2.5"/></svg>
          hello@norvalepartners.com
        </li>
        <li>
          <svg viewBox="0 0 12 12" aria-hidden="true"><circle cx="6" cy="6" r="5"/><path d="M1 6 H11 M6 1 Q3 6 6 11 M6 1 Q9 6 6 11"/></svg>
          www.norvalepartners.com
        </li>
      </ul>
    </div>
  </section>
</main>
</body>
</html>
```